Maplecrest Disability - Social Security Disability Attorneys

Our company is expanding to attract clients nationwide for our social security disability practice. We have a logo, but I am looking for a creative and elegant letterhead that projects an image of being technologically advanced but still professional enough for the legal field. I am looking for the "wow factor" combined with this is still professional enough for a law practice.

Requesting letterhead and business card design
Updates

Had to update and change the logo. The previous logo had a typo. Please send updates with the new logo for consideration. The letterhead and business cards should be professional enough to be used for a law firm. Thanks.

Industry/Entity Type

Law Practice, Law Firm, Healthcare Industry, Government

Colors

Designer to choose colors to be used in the design.

Requirements
Nice to have
• **Please create a vertical design for the business card**

```html
<!DOCTYPE html>
<html lang="en">
<head>
<meta charset="utf-8">
<title>Maplecrest Disability – Business Card</title>
<link rel="stylesheet" href="https://fonts.googleapis.com/css2?family=Libre+Baskerville:wght@400;700&family=Nunito+Sans:wght@400;600&display=swap">
<style>
  :root {
    --page: #8f8f8f;
    --card: #f6f6f5;
    --brand-blue: #4169d8;
    --accent-orange: #ee7a22;
    --ink: #3c3c3c;
    --white: #ffffff;
  }
  * { box-sizing: border-box; margin: 0; padding: 0; }
  html, body { width: 1200px; height: 1200px; overflow: hidden; }
  body {
    background: var(--page);
    font-family: "Nunito Sans", sans-serif;
    position: relative;
  }
  .card {
    position: absolute;
    left: 257px;
    width: 686px;
    height: 392px;
    border-radius: 22px;
    overflow: hidden;
  }
  .card--front { top: 165px; background: var(--card); }
  .card--back { top: 653px; background: var(--brand-blue); }

  .brand {
    position: absolute;
    left: 39px;
    top: 88px;
    width: 310px;
    text-align: center;
    color: var(--brand-blue);
  }
  .brand__name {
    font-family: "Libre Baskerville", serif;
    font-weight: 400;
    font-size: 22px;
    letter-spacing: 2px;
    text-transform: uppercase;
    white-space: nowrap;
  }
  .brand__tagline {
    font-family: "Libre Baskerville", serif;
    font-size: 7px;
    letter-spacing: 2.2px;
    text-transform: uppercase;
    margin-top: 6px;
    white-space: nowrap;
  }

  .address {
    position: absolute;
    left: 39px;
    top: 220px;
    color: var(--ink);
    font-size: 15px;
    line-height: 20px;
  }
  .contact-list {
    position: absolute;
    left: 39px;
    top: 268px;
    list-style: none;
    color: var(--ink);
    font-size: 15px;
    line-height: 19.5px;
  }
  .contact-list li { display: flex; align-items: center; gap: 9px; }
  .contact-list svg { width: 15px; height: 15px; fill: var(--brand-blue); flex: none; }

  .person {
    position: absolute;
    right: 40px;
    top: 262px;
    text-align: right;
  }
  .person__name {
    font-family: "Libre Baskerville", serif;
    font-weight: 700;
    font-size: 20px;
    color: var(--brand-blue);
    letter-spacing: 0.3px;
  }
  .person__role {
    font-size: 14.5px;
    color: var(--accent-orange);
    margin-top: 1px;
  }
  .card__band {
    position: absolute;
    left: 0; right: 0; bottom: 0;
    height: 14px;
    background: var(--brand-blue);
  }

  .back-brand {
    position: absolute;
    left: 0; right: 0;
    top: 150px;
    text-align: center;
    color: var(--white);
  }
  .back-brand__dot {
    display: block;
    width: 34px; height: 34px;
    border-radius: 50%;
    background: var(--white);
    margin: 0 auto 20px;
  }
  .back-brand__name {
    font-family: "Libre Baskerville", serif;
    font-size: 26px;
    letter-spacing: 3px;
    text-transform: uppercase;
  }
  .back-url {
    position: absolute;
    left: 0; right: 0;
    top: 343px;
    text-align: center;
    color: var(--white);
    font-size: 15px;
    letter-spacing: 3.2px;
  }
</style>
</head>
<body>
  <section class="card card--front">
    <div class="brand">
      <div class="brand__name">Maplecrest Disability</div>
      <div class="brand__tagline">Social Security Disability Attorneys</div>
    </div>

    <p class="address">4120 Alder Crest Road<br>Juneau, Alaska 99801</p>

    <ul class="contact-list">
      <li>
        <svg viewBox="0 0 24 24" aria-hidden="true"><path d="M6.6 10.8a15.1 15.1 0 0 0 6.6 6.6l2.2-2.2c.3-.3.7-.4 1-.2 1.1.4 2.3.6 3.6.6.6 0 1 .4 1 1V20c0 .6-.4 1-1 1C10.6 21 3 13.4 3 4c0-.6.4-1 1-1h3.5c.6 0 1 .4 1 1 0 1.3.2 2.5.6 3.6.1.3 0 .7-.2 1z"/></svg>
        555-214-7730
      </li>
      <li>
        <svg viewBox="0 0 24 24" aria-hidden="true"><path d="M7 1h10a2 2 0 0 1 2 2v18a2 2 0 0 1-2 2H7a2 2 0 0 1-2-2V3a2 2 0 0 1 2-2zm0 3v14h10V4zm5 15.2a1.2 1.2 0 1 0 0 2.4 1.2 1.2 0 0 0 0-2.4z"/></svg>
        555-309-8841
      </li>
      <li>
        <svg viewBox="0 0 24 24" aria-hidden="true"><path d="M2 6h20v13H2zm2 2v.4l8 5 8-5V8l-8 5z"/></svg>
        info@maplecrestdisability.com
      </li>
      <li>
        <svg viewBox="0 0 24 24" aria-hidden="true"><path d="M12 2a10 10 0 1 0 0 20 10 10 0 0 0 0-20zm-1 17.9A8 8 0 0 1 4.1 10L9 15v1a2 2 0 0 0 2 2zm6.9-2.5A2 2 0 0 0 16 16h-1v-3a1 1 0 0 0-1-1H8v-2h2a1 1 0 0 0 1-1V7h2a2 2 0 0 0 2-2v-.4a8 8 0 0 1 2.9 12.8z"/></svg>
        www.maplecrestdisability.com
      </li>
    </ul>

    <div class="person">
      <div class="person__name">DANIEL WHITMORE</div>
      <div class="person__role">Founder &amp; CEO</div>
    </div>

    <div class="card__band"></div>
  </section>

  <section class="card card--back">
    <div class="back-brand">
      <span class="back-brand__dot"></span>
      <div class="back-brand__name">Maplecrest Disability</div>
    </div>
    <div class="back-url">www.MaplecrestDisability.com</div>
  </section>
</body>
</html>
```